Marwick Law Letterhead

We need a new letterhead design for a Law Firm. The address for the law firm is 1475 Calloway Street, Suite 210, Houston, Texas 77041. Phone Number: 832-361-9027; Fax Number: 832-614-7359. The logo is uploaded to the project.

```html
<!DOCTYPE html>
<html lang="en">
<head>
<meta charset="utf-8">
<title>Marwick Law Letterhead</title>
<link href="https://fonts.googleapis.com/css2?family=Poppins:wght@400;500;600;700&display=swap" rel="stylesheet">
<style>
  :root {
    --navy: #1d2f5e;
    --red: #e3151f;
    --maroon: #7a0d12;
    --ink: #1b1b1b;
    --paper: #ffffff;
    --backdrop: #ffffff;
  }
  * { margin: 0; padding: 0; box-sizing: border-box; }
  html, body {
    width: 1200px; height: 2859px; overflow: hidden;
    background: var(--backdrop);
    font-family: "Poppins", sans-serif;
    color: var(--ink);
  }
  .letterhead {
    position: absolute; left: 184px; top: 841px;
    width: 832px; height: 1176px;
    background: var(--paper);
    box-shadow: 0 4px 18px rgba(0,0,0,0.22);
    overflow: hidden;
  }
  .header-art { position: absolute; left: 0; top: 0; width: 832px; height: 112px; }
  .firm-name {
    position: absolute; left: 58px; top: 40px;
    display: flex; align-items: center; gap: 10px;
    color: #fff; font-weight: 500; font-size: 24px; line-height: 34px; letter-spacing: 0.3px;
  }
  .firm-name .dot { width: 14px; height: 14px; border-radius: 50%; background: #fff; }
  .contact {
    position: absolute;
    font-size: 14px; line-height: 19.5px;
  }
  .contact li { list-style: none; display: flex; align-items: center; gap: 13px; }
  .contact svg { width: 15px; height: 15px; flex: none; }
  .contact-phones { left: 328px; top: 44px; }
  .contact-phones .num { font-weight: 600; }
  .contact-location { left: 568px; top: 41px; }
  .contact-location li { align-items: flex-start; }
  .contact-location svg { margin-top: 2px; }
  .salutation { position: absolute; left: 62px; top: 235px; font-size: 19px; line-height: 26px; }
  .body-copy {
    position: absolute; left: 58px; top: 275px; width: 706px;
    font-size: 12px; line-height: 16.7px; letter-spacing: -0.25px;
  }
  .body-copy p + p { margin-top: 17.7px; }
  .body-copy .ln {
    display: block; white-space: nowrap;
    text-align: justify; text-align-last: justify;
  }
  .body-copy .ln.end { text-align-last: left; }
  .signature { position: absolute; left: 57px; top: 926px; }
  .signature .line { width: 306px; border-top: 2px dashed #333; margin-left: 9px; margin-bottom: 14px; }
  .signature .name { font-size: 21px; font-weight: 700; line-height: 28px; letter-spacing: -0.3px; }
  .signature .role { font-size: 19px; line-height: 28px; }
  .footer-art { position: absolute; left: 0; top: 1076px; width: 832px; height: 100px; }
</style>
</head>
<body>
  <article class="letterhead">
    <svg class="header-art" viewBox="0 0 832 112" aria-hidden="true">
      <rect x="320" y="0" width="512" height="7" fill="var(--red)"/>
      <path d="M0 0 H330 C305 2 295 22 285 48 C270 92 250 106 215 107 H0 Z" fill="var(--navy)"/>
      <path d="M333 0 C310 4 300 26 290 52 C276 92 255 108 222 108" fill="none" stroke="var(--red)" stroke-width="4"/>
    </svg>
    <div class="firm-name"><span class="dot"></span>Marwick Law</div>

    <ul class="contact contact-phones">
      <li><svg viewBox="0 0 16 16"><path d="M3 1.5 5.6 1 7 4.4 5.3 5.6c.8 1.9 2.2 3.3 4.1 4.1L10.6 8 14 9.4 13.5 12c-.2.9-1 1.4-1.9 1.3C6.4 12.7 2.3 8.6 1.7 3.4 1.6 2.5 2.1 1.7 3 1.5Z" fill="var(--red)"/></svg><span class="num">832-361-9027</span></li>
      <li><svg viewBox="0 0 16 16"><rect x="4" y="1" width="8" height="4" fill="var(--red)"/><rect x="1" y="6" width="14" height="6" rx="1" fill="var(--red)"/><rect x="4" y="10" width="8" height="5" fill="#fff" stroke="var(--red)" stroke-width="1.5"/></svg><span class="num">832-614-7359</span></li>
      <li><svg viewBox="0 0 16 16"><rect x="1" y="3" width="14" height="10" rx="1" fill="var(--red)"/><path d="M1.5 4 8 9l6.5-5" fill="none" stroke="#fff" stroke-width="1.3"/></svg><span>contact@marwickinjury.co</span></li>
    </ul>

    <ul class="contact contact-location">
      <li><svg viewBox="0 0 16 16"><path d="M8 1a4.5 4.5 0 0 0-4.5 4.5C3.5 9 8 13 8 13s4.5-4 4.5-7.5A4.5 4.5 0 0 0 8 1Z" fill="none" stroke="var(--red)" stroke-width="1.8"/><circle cx="8" cy="5.5" r="1.6" fill="var(--red)"/><path d="M2 14.5h12" stroke="var(--red)" stroke-width="1.6"/></svg><span>1475 Calloway Street, Suite<br>210, Houston, Texas 77041</span></li>
      <li><svg viewBox="0 0 16 16"><circle cx="8" cy="8" r="6.5" fill="none" stroke="var(--red)" stroke-width="1.5"/><ellipse cx="8" cy="8" rx="2.8" ry="6.5" fill="none" stroke="var(--red)" stroke-width="1.2"/><path d="M1.5 8h13M2.5 4.8h11M2.5 11.2h11" stroke="var(--red)" stroke-width="1.1"/></svg><span>www.marwickinjury.com</span></li>
    </ul>

    <p class="salutation">Dear Sir,</p>

    <div class="body-copy">
      <p>
        <span class="ln">Quis ipsum suspendisse ultrices gravida. Risus commodo viverra maecenas accumsan lacus vel facilisis. Lorem</span>
        <span class="ln">ipsum dolor sit amet, consectetur adipiscing elit, sed do eiusmod tempor incididunt ut labore et dolore magna</span>
        <span class="ln">aliqua. Quis ipsum suspendisse ultrices gravida. Risus commodo viverra maecenas accumsan lacus vel facilisis.</span>
        <span class="ln">Lorem ipsum dolor sit amet, consectetur adipiscing elit, sed do eiusmod tempor incididunt ut labore et dolore</span>
        <span class="ln">magna aliqua. Quis ipsum suspendisse ultrices gravida. Risus commodo viverra maecenas accumsan lacus vel</span>
        <span class="ln">facilisis. Lorem ipsum dolor sit amet, consectetur adipiscing elit, sed do eiusmod tempor incididunt ut labore et</span>
        <span class="ln">dolore magna aliqua. Quis ipsum suspendisse ultrices gravida. Risus commodo viverra maecenas accumsan</span>
        <span class="ln end">lacus vel facilisis.</span>
      </p>
      <p>
        <span class="ln">Lorem ipsum dolor sit amet, consectetur adipiscing elit, sed do eiusmod tempor incididunt ut labore et dolore</span>
        <span class="ln">magna aliqua. Quis ipsum suspendisse ultrices gravida. Risus commodo viverra maecenas accumsan lacus vel</span>
        <span class="ln">facilisis. Lorem ipsum dolor sit amet, consectetur adipiscing elit, sed do eiusmod tempor incididunt ut labore et</span>
        <span class="ln">dolore magna aliqua. Quis ipsum suspendisse ultrices gravida. Risus commodo viverra maecenas accumsan</span>
        <span class="ln">lacus vel facilisis. Lorem ipsum dolor sit amet, consectetur adipiscing elit, sed do eiusmod tempor incididunt ut</span>
        <span class="ln">labore et dolore magna aliqua. Quis ipsum suspendisse ultrices gravida. Risus commodo viverra maecenas</span>
        <span class="ln">accumsan lacus vel facilisis. Lorem ipsum dolor sit amet, consectetur adipiscing elit, sed do eiusmod tempor</span>
        <span class="ln">incididunt ut labore et dolore magna aliqua. Quis ipsum suspendisse ultrices gravida. Risus commodo viverra</span>
        <span class="ln end">maecenas accumsan lacus vel facilisis.</span>
      </p>
      <p>
        <span class="ln">Lorem ipsum dolor sit amet, consectetur adipiscing elit, sed do eiusmod tempor incididunt ut labore et dolore</span>
        <span class="ln">magna aliqua. Quis ipsum suspendisse ultrices gravida. Risus commodo viverra maecenas accumsan lacus vel</span>
        <span class="ln">facilisis. Lorem ipsum dolor sit amet, consectetur adipiscing elit, sed do eiusmod tempor incididunt ut labore et</span>
        <span class="ln">dolore magna aliqua. Quis ipsum suspendisse ultrices gravida. Risus commodo viverra maecenas accumsan</span>
        <span class="ln">lacus vel facilisis. Lorem ipsum dolor sit amet, consectetur adipiscing elit, sed do eiusmod tempor incididunt ut</span>
        <span class="ln">labore et dolore magna aliqua. Quis ipsum suspendisse ultrices gravida. Risus commodo viverra maecenas</span>
        <span class="ln">accumsan lacus vel facilisis. Lorem ipsum dolor sit amet, consectetur adipiscing elit, sed do eiusmod tempor</span>
        <span class="ln">incididunt ut labore et dolore magna aliqua. Quis ipsum suspendisse ultrices gravida. Risus commodo viverra</span>
        <span class="ln">maecenas accumsan lacus vel facilisis. Lorem ipsum dolor sit amet, consectetur adipiscing elit, sed do eiusmod</span>
        <span class="ln">tempor incididunt ut labore et dolore magna aliqua. Quis ipsum suspendisse ultrices gravida. Risus commodo</span>
        <span class="ln">viverra maecenas accumsan lacus vel facilisis. Lorem ipsum dolor sit amet, consectetur adipiscing elit, sed do</span>
        <span class="ln">eiusmod tempor incididunt ut labore et dolore magna aliqua. Quis ipsum suspendisse ultrices gravida. Risus</span>
        <span class="ln end">commodo viverra maecenas accumsan lacus vel facilisis.</span>
      </p>
    </div>

    <div class="signature">
      <div class="line"></div>
      <div class="name">Graham T Ellison III</div>
      <div class="role">Attorney at Law</div>
    </div>

    <svg class="footer-art" viewBox="0 0 832 100" aria-hidden="true">
      <path d="M0 36 C150 78 330 88 480 86 C620 84 720 58 790 62 C810 63 822 72 832 86 V100 H0 Z" fill="var(--navy)"/>
      <path d="M0 0 C120 45 300 78 520 84 C320 82 140 60 0 22 Z" fill="var(--maroon)"/>
    </svg>
  </article>
</body>
</html>
```